Business Cards for company that supports physicians that do medical research

Need to create a business card for Qorvel Studies (www.qorvelstudies.example), a company devoted to supporting physicians who conduct medical research. The form of the card should match the message of research and information quest. I have provided the logo of the company as an uploaded file. Designs should be simple and slick aimed at very high end clients.

Target Market(s)

Medical doctors that are also researchers

Industry/Entity Type

Medical

Contact Information for Business Card

Should feature logo and fields for personal info:
Name/title
Phone /email

Font styles to use
Serif
Sans Serif

Requirements
Must have
• Qorvel logo and fields for personal info:
• Name: Bertrand Okonfu
• Title: VP Research and Senior Analyst
• Phone: 555-203-4719
• email: info@qorvelstudies.example
Nice to have
• Interesting cards that I've seen:
• 1- all black/charcoal or very dark background
• 2- Plastic - semi-transparent
• 3- non-standard height-width ratios
• 4- Functional cards -- USB drive incorporated
Should not have
• Too busy; needs to stay very simple

```html
<!DOCTYPE html>
<html lang="en">
<head>
<meta charset="utf-8">
<title>Qorvel Studies – Business Card</title>
<link rel="stylesheet" href="https://fonts.googleapis.com/css2?family=Source+Sans+3:ital,wght@0,400;0,600;1,400&display=swap">
<style>
  :root {
    --backdrop: #3b3b3b;
    --card-white: #fbfbfb;
    --brand-blue: #1b7bc0;
    --brand-green: #45b649;
    --accent-grey: #5a5a5a;
    --ink-white: #ffffff;
  }
  * { box-sizing: border-box; margin: 0; padding: 0; }
  html, body {
    width: 1200px; height: 750px; overflow: hidden;
    background: var(--backdrop);
    font-family: "Source Sans 3", "Helvetica Neue", Arial, sans-serif;
  }
  .stage { position: relative; width: 1200px; height: 750px; }
  .card {
    position: absolute; top: 228px;
    width: 461px; height: 262px; overflow: hidden;
  }
  .card--front { left: 124px; background: var(--card-white); }
  .card--back { left: 618px; background: var(--brand-blue); }
  .card__shape { position: absolute; inset: 0; }

  .brand-name {
    position: absolute; left: 50px; top: 40px;
    color: var(--brand-blue); font-weight: 600; line-height: 1;
  }
  .brand-name__main { display: block; font-size: 46px; letter-spacing: -0.5px; }
  .brand-name__sub { display: block; font-size: 19px; letter-spacing: 6.5px; margin-top: 6px; padding-left: 2px; }

  .contact {
    position: absolute; right: 25px; top: 150px;
    color: var(--ink-white); text-align: right;
  }
  .contact__name { font-size: 17px; font-weight: 600; line-height: 1.1; }
  .contact__title { font-size: 12.5px; margin-top: 3px; }
  .contact__list { list-style: none; margin-top: 8px; }
  .contact__item {
    display: flex; justify-content: flex-end; align-items: center;
    font-size: 11px; height: 17.5px; gap: 6px;
  }
  .contact__icon { width: 11px; height: 11px; flex: none; }

  .back-pattern { position: absolute; inset: 0; background: var(--brand-blue); }
  .back-brand {
    position: absolute; left: 0; right: 0; top: 90px;
    color: var(--ink-white); font-weight: 600; text-align: center; line-height: 1;
  }
  .back-brand__main { display: block; font-size: 50px; letter-spacing: -0.5px; }
  .back-brand__sub { display: block; font-size: 20px; letter-spacing: 7px; margin-top: 6px; }
  .back-url {
    position: absolute; left: 0; right: 0; top: 207px;
    color: var(--ink-white); text-align: center;
    font-size: 11px; font-style: italic; letter-spacing: 2.4px;
  }
</style>
</head>
<body>
<main class="stage">

  <section class="card card--front" aria-label="Card front">
    <svg class="card__shape" viewBox="0 0 461 262" aria-hidden="true">
      <path d="M244 0 C268 20 276 50 262 80 C246 115 214 150 208 196 C205 225 216 248 232 262 L461 262 L461 0 Z" fill="var(--brand-blue)"/>
      <path d="M236 0 C262 18 270 48 258 80" fill="none" stroke="var(--accent-grey)" stroke-width="3" stroke-linecap="round"/>
      <path d="M230 140 C210 165 200 200 206 225 C210 243 218 254 226 262" fill="none" stroke="var(--brand-green)" stroke-width="3" stroke-linecap="round"/>
    </svg>

    <div class="brand-name">
      <span class="brand-name__main">Qorvel</span>
      <span class="brand-name__sub">STUDIES</span>
    </div>

    <div class="contact">
      <p class="contact__name">Bertrand Okonfu</p>
      <p class="contact__title">VP Research &amp; Senior Analyst</p>
      <ul class="contact__list">
        <li class="contact__item">555-203-4719
          <svg class="contact__icon" viewBox="0 0 12 12" aria-hidden="true"><path d="M2.5 0.8 L4.4 2.9 L3.4 4.2 C4 5.7 6.2 7.9 7.8 8.6 L9.1 7.6 L11.2 9.5 L9.8 11.2 C5.6 11 1 6.4 0.8 2.2 Z" fill="#fff"/></svg>
        </li>
        <li class="contact__item">info@qorvelstudies.example
          <svg class="contact__icon" viewBox="0 0 12 12" aria-hidden="true"><rect x="0.5" y="2.5" width="11" height="7.5" fill="#fff"/><path d="M0.8 2.8 L6 7 L11.2 2.8" fill="none" stroke="var(--brand-blue)" stroke-width="1"/></svg>
        </li>
        <li class="contact__item">www.qorvelstudies.example
          <svg class="contact__icon" viewBox="0 0 12 12" aria-hidden="true"><circle cx="6" cy="6" r="5.5" fill="#fff"/><path d="M3 3.5 C4.5 4 5 5.5 4 7 M7.5 2 C7 4 9 5 10.5 5 M6.5 8 C7.5 9 8 10 7.5 11" fill="none" stroke="var(--brand-blue)" stroke-width="1.2"/></svg>
        </li>
      </ul>
    </div>
  </section>

  <section class="card card--back" aria-label="Card back">
    <div class="back-pattern" role="img" aria-label="Faint repeated brand name pattern in lighter blue"></div>
    <div class="back-brand">
      <span class="back-brand__main">Qorvel</span>
      <span class="back-brand__sub">STUDIES</span>
    </div>
    <p class="back-url">www.qorvelstudies.example</p>
  </section>

</main>
</body>
</html>
```